Web Design for a Biotech Consulting Firm

We need a web site design for a new business based in Philadelphia called Verantel Dx. This is a consulting firm that will serve medical diagnostics industry, which is part of the life science/healthcare industry focusing on developing and marketing products that help in early detection, monitoring or management of diseases. Our consulting firm will help medical diagnostic companies to overcome key challenges in designing, evaluating and marketing new products.Our company name is Verantel Dx. Verantel is Latin word for "something" Dx represents diagnostics. The idea behind the name is that we help companies to transform the original, early product ideas ("nothing") into "something"; which is a product with full clinical utility that will help to improve health and well-being.The web site should use the visual feel of the logo (attached), be modern, simple and clean looking and represent creativity, innovation, scientific thinking and progress.
Updates

Wix Design is acceptable

Industry/Entity Type

(plain badge)

Coding

Coded - Design and coding required

Number of Pages Required

1 page

Font styles to use
Sans Serif

Requirements
Must have
• simple, clean look couple of pages
Should not have
• a lot of pages

```html
<!DOCTYPE html>
<html lang="en">
<head>
<meta charset="utf-8">
<title>Verantel Dx — Biotech Consulting</title>
<link href="https://fonts.googleapis.com/css2?family=Montserrat:wght@300;400;500;700;800&family=Lato:wght@400;700&display=swap" rel="stylesheet">
<style>
:root{
  --blue:#2f86f0;
  --ink:#1b1b1b;
  --text:#333;
  --footer:#111214;
  --white:#fff;
}
*{box-sizing:border-box;margin:0;padding:0}
html,body{width:1200px;height:3019px;overflow:hidden;background:var(--white)}
body{font-family:"Lato",sans-serif;color:var(--text);position:relative}
section,header,footer{position:relative;width:1200px}
.abs{position:absolute}
a{color:inherit;text-decoration:none}

/* header */
.site-header{height:110px;background:var(--white)}
.brand{left:115px;top:40px;font-family:"Montserrat",sans-serif;font-weight:500;font-size:20px;color:var(--ink);white-space:nowrap}
.main-nav{left:429px;top:50px;display:flex}
.main-nav a{font-family:"Montserrat",sans-serif;font-size:15px;color:#222;padding:4px 8px;margin-right:44px;white-space:nowrap}
.main-nav a.active{color:var(--blue);border:1px solid var(--blue)}
.nav-divider{left:897px;top:22px;width:1px;height:70px;background:#e4e4e4}
.call{left:928px;top:28px;width:170px;text-align:center;white-space:nowrap}
.call-label{display:inline-block;font-family:"Montserrat",sans-serif;font-size:18px;letter-spacing:1.5px;color:#222;padding:0 8px 4px;border-bottom:2px solid #222}
.call-phone{font-family:"Montserrat",sans-serif;font-weight:700;font-size:21px;color:var(--blue);margin-top:6px}

/* hero */
.hero{height:563px;background:linear-gradient(100deg,#d9ecf8 0%,#8fc8f2 30%,#bfe0f7 55%,#e6f2fb 100%);overflow:hidden}
.hero-headline{right:113px;top:222px;text-align:right;font-family:"Montserrat",sans-serif;font-weight:800;font-size:33px;line-height:44px;color:#111;white-space:nowrap}
.hero-arrows{left:1021px;top:371px;display:flex;gap:10px}
.hero-arrows span{width:28px;height:28px;border:1px solid #222;display:flex;align-items:center;justify-content:center}

/* section titles */
.title{width:1200px;text-align:center;font-family:"Montserrat",sans-serif;font-weight:400;font-size:33px;color:#222;letter-spacing:.5px}
.title em{font-style:normal;color:var(--blue)}
.rule{left:534px;width:132px;height:2px;background:linear-gradient(90deg,#222 50%,var(--blue) 50%)}
.rule.light{background:linear-gradient(90deg,#1d3e6a 50%,#9ec8f8 50%)}

/* welcome */
.welcome{height:464px}
.welcome .lede{top:150px;width:1200px;text-align:center;color:var(--blue);font-size:15px;line-height:23px}
.welcome .body{top:210px;left:145px;width:910px;text-align:center;font-size:13.5px;line-height:23px;color:#222}
.pillar{top:315px;display:flex;gap:14px}
.pillar-icon{width:66px;height:66px;border:1px solid var(--blue);display:flex;align-items:center;justify-content:center}
.pillar h3{font-family:"Montserrat",sans-serif;font-weight:500;font-size:17px;color:#111;margin-top:2px}
.pillar p{font-size:13.5px;line-height:22px;color:#222;margin-top:6px;margin-left:2px;white-space:nowrap}
.pillar p span{color:var(--blue)}

/* services */
.services{height:544px;background:linear-gradient(120deg,#3b8ef2 0%,#3e8ff0 40%,#2f82ea 70%,#3a8df0 100%);color:var(--white)}
.services .title{color:#1b1b1b}
.services .sub{top:158px;width:1200px;text-align:center;font-size:16px;color:var(--white)}
.service{top:228px;width:300px;text-align:center}
.service svg{display:block;margin:0 auto}
.service h3{font-family:"Montserrat",sans-serif;font-weight:700;font-size:20px;margin-top:20px;letter-spacing:.3px;white-space:nowrap}
.service p{font-size:14px;line-height:22px;margin-top:14px}
.btn-outline{display:inline-block;margin-top:24px;width:120px;height:36px;line-height:34px;border:1px solid var(--white);font-family:"Montserrat",sans-serif;font-size:15px;letter-spacing:.5px}

/* news */
.news{height:415px}
.news-card{top:165px;width:300px}
.date{display:inline-block;background:var(--blue);color:var(--white);font-family:"Montserrat",sans-serif;font-size:13px;padding:7px 11px;box-shadow:2px 2px 0 #cfe2fb}
.news-card h3{font-family:"Montserrat",sans-serif;font-weight:700;font-size:14.5px;color:#222;margin-top:18px;white-space:nowrap}
.news-card p{font-size:13.5px;line-height:22px;color:#222;margin-top:6px;width:285px}
.news-card a{display:inline-block;margin-top:12px;font-size:12px;font-weight:700;color:var(--blue);text-decoration:underline}
.chev{font-family:"Montserrat",sans-serif;font-size:40px;font-weight:300;color:#999;top:245px}

/* cta */
.cta{height:262px;background:linear-gradient(90deg,#2b2c2f 0%,#232427 50%,#2e2e30 100%);color:var(--white)}
.cta h2{left:115px;top:78px;font-family:"Montserrat",sans-serif;font-weight:800;font-size:35px;white-space:nowrap}
.cta p{left:115px;top:139px;width:430px;font-size:15px;line-height:25px}
.btn-ghost{left:876px;top:105px;width:191px;height:52px;border:2px solid var(--white);display:flex;align-items:center;justify-content:center;font-family:"Montserrat",sans-serif;font-weight:700;font-size:19px;letter-spacing:1px}

/* partners */
.partners{height:332px}
.partner{top:181px;width:141px;height:66px;border:1px solid #d3d3d3;display:flex;align-items:center;justify-content:center}
.partner.active{border-color:var(--blue)}
.partner i{display:block;width:70px;height:26px;background:#c9c9c9;border-radius:4px}

/* footer */
.site-footer{height:295px;background:var(--footer);color:var(--white)}
.col-title{top:54px;font-family:"Montserrat",sans-serif;font-weight:400;font-size:17px;letter-spacing:.4px;white-space:nowrap}
.col-rule{top:82px;width:44px;height:2px;background:var(--blue)}
.vline{top:82px;width:1px;height:160px;background:#2a2b2e}
.links{left:115px;top:108px;list-style:none}
.links li{font-size:12.5px;line-height:32px;padding-left:12px;position:relative}
.links li::before{content:"";position:absolute;left:0;top:15px;width:3px;height:3px;background:var(--blue);border-radius:50%}
.contact-row{left:325px;display:flex;gap:14px;font-size:12.5px;line-height:17px}
.field{left:641px;width:225px;height:29px;background:var(--white);color:#999;font-size:11px;padding:8px 10px}
.submit{left:641px;top:220px;width:104px;height:29px;background:var(--blue);color:var(--white);font-weight:700;font-size:13px;display:flex;align-items:center;justify-content:center}
.social{left:980px;display:flex;align-items:center;gap:9px;font-family:"Montserrat",sans-serif;font-size:12px;font-weight:500}
.social span{width:28px;height:28px;border:1px solid #bbb}
.copyright{height:34px;background:var(--blue);color:var(--white);text-align:center;font-size:11.5px;line-height:34px}
</style>
</head>
<body>

<header class="site-header">
  <div class="brand abs">Verantel Dx</div>
  <nav class="main-nav abs">
    <a class="active" href="#">Home</a><a href="#">About Us</a><a href="#">Services</a><a href="#">Contact Us</a>
  </nav>
  <div class="nav-divider abs"></div>
  <div class="call abs">
    <div class="call-label">Call Us Today</div>
    <div class="call-phone">123-456-7890</div>
  </div>
</header>

<section class="hero" role="img" aria-label="Doctor touching a glowing blue interface of hexagons, medical icons and a DNA helix">
  <h1 class="hero-headline abs">We Are A Biotech Consulting<br>Firm Serving The Medical<br>Diagnostics Industry</h1>
  <div class="hero-arrows abs">
    <span><svg width="10" height="12" viewBox="0 0 10 12"><path d="M7 1 2 6l5 5" fill="none" stroke="#222" stroke-width="2"/></svg></span>
    <span><svg width="10" height="12" viewBox="0 0 10 12"><path d="M3 1l5 5-5 5" fill="none" stroke="#222" stroke-width="2"/></svg></span>
  </div>
</section>

<section class="welcome">
  <h2 class="title abs" style="top:75px">Welcome To Verantel Dx</h2>
  <div class="rule abs" style="top:124px"></div>
  <p class="lede abs">Verantel Dx This Is A Consulting Firm That Will Serve Medical Diagnostics Industry,<br>Which Is Part of The Life Science/healthcare Industry</p>
  <p class="body abs">Lorem ipsum dolor sit amet, consectetuer adipiscing elit, sed diam nonummy nibh euismod tincidunt ut laoreet dolore magna aliquam erat volutpat. Ut wisi enim ad minim veniam, quis nostrud exerci tation ullamcorper suscipit lobortis nisl ut aliquip ex ea commodo consequat. Duis autem vel eum iriure &nbsp;or sit amet, consectetuer adipiscing elit, sed diam nonummy nibh euismod tincidunt ut laoreet dolore magna aliquam erat volutpat. Ut wisi enim</p>
  <div class="pillar abs" style="left:183px">
    <div class="pillar-icon"><svg width="42" height="40" viewBox="0 0 42 40" fill="none" stroke="#222" stroke-width="1.6"><path d="M3 37 16 14l6 9 5-6 12 20z"/><path d="M16 14V3l7 3-7 3"/><path d="M11 28l4-3 4 4 5-3"/></svg></div>
    <div><h3>MISSION</h3><p>Lorem ipsum dolor sit amet, consectetuer adipisci<br>laoreet dolore magna aliquam erat volutpat<span>....(+)</span></p></div>
  </div>
  <div class="pillar abs" style="left:639px">
    <div class="pillar-icon"><svg width="42" height="42" viewBox="0 0 42 42" fill="none" stroke="#222" stroke-width="1.6"><circle cx="26" cy="14" r="6"/><path d="M10 36 22 18M30 18l-12 16M14 38h14"/><path d="M8 8l2 2M6 14h3M34 4l2 2"/></svg></div>
    <div><h3>VISION</h3><p>Lorem ipsum dolor sit amet, consectetuer adipisci<br>laoreet dolore magna aliquam erat volutpat<span>....(+)</span></p></div>
  </div>
</section>

<section class="services" role="img" aria-label="Blue-tinted photo of a hand writing with a pen">
  <h2 class="title abs" style="top:78px">Our <em style="color:#fff">Services</em></h2>
  <div class="rule light abs" style="top:126px"></div>
  <p class="sub abs">Our Consulting Firm Will Help Medical Diagnostic Companies To Overcome Key Challenges In</p>
  <div class="service abs" style="left:88px">
    <svg width="66" height="68" viewBox="0 0 66 68" fill="none" stroke="#fff" stroke-width="2"><rect x="4" y="60" width="58" height="5"/><rect x="10" y="14" width="10" height="46"/><rect x="24" y="4" width="10" height="56"/><rect x="38" y="10" width="10" height="50"/><path d="M52 18l5-8 5 8v42H52z"/><path d="M27 16h4M27 24h4M27 32h4M27 40h4"/></svg>
    <h3>Designing</h3>
    <p>Lorem ipsum dolor sit amet, consectetuer<br>adipiscing elit , sed diam nonummy nibh</p>
    <a class="btn-outline" href="#">READ MORE</a>
  </div>
  <div class="service abs" style="left:441px">
    <svg width="80" height="78" viewBox="0 0 80 78" fill="none" stroke="#fff" stroke-width="2"><rect x="8" y="10" width="44" height="62"/><rect x="22" y="5" width="16" height="9"/><path d="M14 32h8v8h-8zM14 46h8v8h-8zM14 58h8v8h-8zM26 62h10"/><circle cx="42" cy="38" r="12"/><path d="M37 38l4 4 7-8M50 47l12 14"/><path d="M70 4v8M66 8h8"/></svg>
    <h3>Evaluating</h3>
    <p>Lorem ipsum dolor sit amet, consectetuer<br>adipiscing elit , sed diam nonummy nibh</p>
    <a class="btn-outline" href="#">READ MORE</a>
  </div>
  <div class="service abs" style="left:797px">
    <svg width="96" height="68" viewBox="0 0 96 68" fill="none" stroke="#fff" stroke-width="2"><rect x="4" y="6" width="52" height="40"/><path d="M22 46v10M38 46v10M14 58h32"/><path d="M14 14h14v12H14zM18 17l6 3-6 3z"/><path d="M14 32h22M14 38h16"/><path d="M44 18h10l18-10v36L54 34H44z"/><path d="M80 16l8-4M80 26h9M80 36l8 4"/></svg>
    <h3>Marketing New Products</h3>
    <p>Lorem ipsum dolor sit amet, consectetuer<br>adipiscing elit , sed diam nonummy nibh</p>
    <a class="btn-outline" href="#">READ MORE</a>
  </div>
</section>

<section class="news">
  <h2 class="title abs" style="top:76px">Latest <em>News</em></h2>
  <div class="rule abs" style="top:124px"></div>
  <div class="chev abs" style="left:58px">&#8249;</div>
  <article class="news-card abs" style="left:114px">
    <span class="date">JUNE 05, 2019</span>
    <h3>LOREM IPSUM DOLOR SIT AMET NSE</h3>
    <p>Quis nostrud exerci tation ullamcorper suscipit lobortis nisl ut aliquip ex ea commodonsequat Duis autem vel eum iriure</p>
    <a href="#">LEARN MORE</a>
  </article>
  <article class="news-card abs" style="left:458px">
    <span class="date">JUNE 05, 2019</span>
    <h3>SED DIAM NONUMMY NIBH EUISMOD</h3>
    <p>Quis nostrud exerci tation ullamcorper suscipit lobortis nisl ut aliquip ex ea commodonsequat Duis autem vel eum iriure</p>
    <a href="#">LEARN MORE</a>
  </article>
  <article class="news-card abs" style="left:804px">
    <span class="date">JUNE 05, 2019</span>
    <h3>LOREM IPSUM DOLOR SIT AMET NSE</h3>
    <p>Quis nostrud exerci tation ullamcorper suscipit lobortis nisl ut aliquip ex ea commodonsequat Duis autem vel eum iriure</p>
    <a href="#">LEARN MORE</a>
  </article>
  <div class="chev abs" style="left:1122px">&#8250;</div>
</section>

<section class="cta" role="img" aria-label="Dark photo of a scientist looking into a microscope">
  <h2 class="abs">Not Sure of Your Next Step?</h2>
  <p class="abs">Lorem ipsum dolor sit amet, consectetuer adipiscing elit, sed nonummy nibh euismod tincidunt ut laoreet dolore</p>
  <a class="btn-ghost abs" href="#">GET STARTED</a>
</section>

<section class="partners">
  <h2 class="title abs" style="top:96px">Our <em>Partners</em></h2>
  <div class="rule abs" style="top:146px"></div>
  <svg class="abs" style="left:48px;top:196px" width="22" height="40" viewBox="0 0 22 40"><path d="M20 2 3 20l17 18" fill="none" stroke="#bbb" stroke-width="2"/></svg>
  <div class="partner active abs" style="left:113px"><i></i></div>
  <div class="partner abs" style="left:279px"><i></i></div>
  <div class="partner abs" style="left:446px"><i></i></div>
  <div class="partner abs" style="left:612px"><i></i></div>
  <div class="partner abs" style="left:779px"><i></i></div>
  <div class="partner abs" style="left:946px"><i></i></div>
  <svg class="abs" style="left:1114px;top:196px" width="22" height="40" viewBox="0 0 22 40"><path d="M2 2l17 18L2 38" fill="none" stroke="#bbb" stroke-width="2"/></svg>
</section>

<footer class="site-footer">
  <h4 class="col-title abs" style="left:115px">Quick Links</h4>
  <div class="col-rule abs" style="left:140px"></div>
  <ul class="links abs"><li>Home</li><li>About Us</li><li>Services</li><li>Contact Us</li></ul>
  <div class="vline abs" style="left:270px"></div>

  <h4 class="col-title abs" style="left:325px">Contact Details</h4>
  <div class="col-rule abs" style="left:368px"></div>
  <div class="contact-row abs" style="top:108px"><svg width="14" height="18" viewBox="0 0 14 18"><path d="M7 1a6 6 0 0 0-6 6c0 4 6 10 6 10s6-6 6-10a6 6 0 0 0-6-6z" fill="var(--blue)"/><circle cx="7" cy="7" r="2.2" fill="#111"/></svg><span>123 Loren Ipsum dolor mnwp<br>AB Mnwrr Conr 1234</span></div>
  <div class="contact-row abs" style="top:164px"><svg width="14" height="14" viewBox="0 0 14 14"><path d="M3 1l3 3-2 2c1 2 2 3 4 4l2-2 3 3-2 2C6 13 1 8 1 3z" fill="var(--blue)"/></svg><span>123-456-7890</span></div>
  <div class="contact-row abs" style="top:209px"><svg width="15" height="12" viewBox="0 0 15 12"><rect width="15" height="12" fill="var(--blue)"/><path d="M0 0l7.5 6L15 0" fill="none" stroke="#111" stroke-width="1.4"/></svg><span>info@veranteldx.com</span></div>
  <div class="vline abs" style="left:582px"></div>

  <h4 class="col-title abs" style="left:639px">Quick Inquiry</h4>
  <div class="col-rule abs" style="left:676px"></div>
  <div class="field abs" style="top:112px">Name</div>
  <div class="field abs" style="top:148px">Email</div>
  <div class="field abs" style="top:183px">Message</div>
  <div class="submit abs">Submit</div>
  <div class="vline abs" style="left:921px"></div>

  <h4 class="col-title abs" style="left:976px">Follow Us</h4>
  <div class="col-rule abs" style="left:1020px"></div>
  <div class="social abs" style="top:112px"><span></span>FRIENDBOOK</div>
  <div class="social abs" style="top:158px"><span></span>CHIRPER</div>
  <div class="social abs" style="top:204px"><span></span>WORKLINK</div>
</footer>

<div class="copyright">Copyright © 2019 Verantel Dx . All Rights Reserved.</div>

</body>
</html>
```